SaaS Early tech startup business card design

Unique design for experience ecommerce platform company. the business cards will be used by executive members. conformance with color code is required.

```html
<!DOCTYPE html>
<html lang="en">
<head>
<meta charset="utf-8">
<title>Velora Business Card</title>
<link href="https://fonts.googleapis.com/css2?family=Arimo:wght@400;700&display=swap" rel="stylesheet">
<style>
  :root {
    --bg: #1c1c1e;
    --card-white: #ffffff;
    --card-navy: #222238;
    --teal: #0f8c95;
    --teal-bright: #1aa79c;
    --ink: #222222;
    --rule: #9a9a9a;
  }
  * { box-sizing: border-box; margin: 0; padding: 0; }
  html, body {
    width: 1200px; height: 900px; overflow: hidden;
    background: var(--bg);
    font-family: "Arimo", Arial, sans-serif;
  }
  .stage {
    width: 1200px; height: 900px;
    display: flex; flex-direction: column; align-items: center; justify-content: center;
    gap: 48px;
  }
  .card {
    width: 595px; height: 340px;
    box-shadow: 0 12px 30px rgba(0,0,0,0.55);
    position: relative;
  }
  .card-front { background: var(--card-white); color: var(--ink); }
  .card-back {
    background: var(--card-navy);
    display: flex; align-items: center; justify-content: center;
  }
  .identity {
    position: absolute; top: 92px; left: 0; right: 0;
    text-align: center;
  }
  .identity-name {
    color: var(--teal); font-weight: 700; font-size: 21px; letter-spacing: 0.5px;
  }
  .identity-title { font-size: 14px; margin-top: 3px; }
  .details {
    position: absolute; top: 160px; left: 0; right: 0;
    display: flex; justify-content: center; align-items: stretch;
  }
  .address {
    text-align: right; font-size: 14px; line-height: 20px;
    padding: 10px 20px 0 0; width: 230px;
  }
  .divider { width: 1px; background: var(--rule); height: 72px; }
  .contacts {
    list-style: none; font-size: 14px; line-height: 21px;
    padding-left: 18px; width: 240px;
  }
  .contacts li { display: flex; align-items: center; gap: 7px; }
  .contacts svg { width: 13px; height: 13px; flex: none; }
  .brand-name {
    color: var(--teal-bright); font-weight: 700; font-size: 96px; letter-spacing: 2px;
    text-transform: lowercase;
  }
</style>
</head>
<body>
<main class="stage">
  <section class="card card-front">
    <div class="identity">
      <h1 class="identity-name">MARCUS ELLERY</h1>
      <p class="identity-title">Managing Director</p>
    </div>
    <div class="details">
      <address class="address" style="font-style:normal">
        421 , Address<br>line goes here<br>45452,Country Name
      </address>
      <div class="divider"></div>
      <ul class="contacts">
        <li>
          <svg viewBox="0 0 16 16" aria-hidden="true"><path fill="#0f8c95" d="M3.5 1.5l2.5 0 1 3.5-1.6 1.2a8 8 0 0 0 4.4 4.4L11 9l3.5 1v2.5c0 1-1 2-2 2A11 11 0 0 1 1.5 3.5c0-1 1-2 2-2z"/></svg>
          044-555 018 274
        </li>
        <li>
          <svg viewBox="0 0 16 16" aria-hidden="true"><rect x="1" y="3" width="14" height="10" fill="#0f8c95"/><path d="M1 3l7 6 7-6" fill="none" stroke="#fff" stroke-width="1.2"/></svg>
          hello@velora.io
        </li>
        <li>
          <svg viewBox="0 0 16 16" aria-hidden="true"><g fill="none" stroke="#0f8c95" stroke-width="1.3"><circle cx="8" cy="8" r="6.5"/><ellipse cx="8" cy="8" rx="3" ry="6.5"/><path d="M1.5 8h13M2.5 4.8h11M2.5 11.2h11"/></g></svg>
          www.velora.io
        </li>
      </ul>
    </div>
  </section>
  <section class="card card-back">
    <span class="brand-name">velora</span>
  </section>
</main>
</body>
</html>
```